Veltrane Group Business Card Design

The CEO is looking for a new trendy look for his business card.
You can stay with current branding or come up with something new/creative. It can be 3D, including Medical Office buildings. You can use our logo in a variety of colors. Please include name, title, company name, company website, email address, cell number

Target Market(s)

Real Estate Development and Construction

Industry/Entity Type

Health care real estate

Contact Information for Business Card

Rohesh Kamdar, CEO M-604.781.2249 E-roheshkamdar@veltrane.com Address:4180 Lindqvist Ave, Tampa, FL 33482 www.veltrane.com

Font styles to use
Other font styles liked:
• Be creative

Requirements
Must have
• Creative, trendy look
Nice to have
• Please go to our website to get a feel- www. veltrane.com
Should not have
• small fonts

```html
<!DOCTYPE html>
<html lang="en">
<head>
<meta charset="utf-8">
<title>Veltrane Group – Business Card</title>
<link rel="stylesheet" href="https://fonts.googleapis.com/css2?family=Montserrat:wght@400;500;700;800&display=swap">
<style>
  :root {
    --bg: #2a2a2c;
    --card: #ffffff;
    --red: #b01f2a;
    --navy: #1d3052;
    --ink-light: #ffffff;
    --ink-grey: #3a3a3a;
  }
  * { box-sizing: border-box; margin: 0; padding: 0; }
  html, body {
    width: 1200px; height: 900px; overflow: hidden;
    background: var(--bg);
    font-family: "Montserrat", sans-serif;
  }
  .canvas { position: relative; width: 1200px; height: 900px; }
  .card {
    position: absolute; left: 250px;
    width: 700px; height: 400px;
    background: var(--card);
    border-radius: 22px; overflow: hidden;
  }
  .card--front { top: 40px; }
  .card--back { top: 470px; }
  .card__art { position: absolute; inset: 0; width: 100%; height: 100%; }

  .brand {
    position: absolute; color: var(--red);
    font-weight: 800; letter-spacing: -1px; white-space: nowrap;
  }
  .card--front .brand { right: 44px; top: 40px; font-size: 50px; }
  .card--back .brand {
    left: 0; right: 0; top: 0; bottom: 0;
    display: flex; align-items: center; justify-content: center;
    font-size: 72px;
  }

  .person { position: absolute; right: 48px; top: 252px; text-align: right; }
  .person__name { color: var(--red); font-weight: 700; font-size: 24px; letter-spacing: 0.5px; white-space: nowrap; }
  .person__title { color: var(--ink-grey); font-weight: 400; font-size: 17px; margin-top: 2px; }
  .accent-bar { position: absolute; right: 0; top: 248px; width: 22px; height: 62px; background: var(--red); }

  .contact { position: absolute; left: 46px; top: 232px; color: var(--ink-light); list-style: none; }
  .contact li { display: flex; align-items: flex-start; gap: 12px; font-size: 17px; line-height: 1.3; margin-bottom: 8px; white-space: nowrap; }
  .contact svg { width: 16px; height: 16px; flex: none; margin-top: 3px; fill: var(--red); }
</style>
</head>
<body>
<main class="canvas">

  <section class="card card--front" aria-label="Business card front">
    <svg class="card__art" viewBox="0 0 700 400" preserveAspectRatio="none" aria-hidden="true">
      <path d="M8,100 C120,132 250,112 320,104" fill="none" stroke="var(--red)" stroke-width="4"/>
      <path d="M0,112 C120,148 250,124 320,122 C380,120 400,220 415,400 L398,400 C392,300 370,190 330,178 C250,165 140,178 0,152 Z" fill="var(--red)"/>
      <path d="M0,157 C140,183 250,170 326,183 C362,195 386,300 393,400 L0,400 Z" fill="var(--navy)"/>
    </svg>

    <div class="brand">Veltrane Group</div>

    <div class="accent-bar"></div>
    <div class="person">
      <div class="person__name">ROHESH KAMDAR</div>
      <div class="person__title">CEO</div>
    </div>

    <ul class="contact">
      <li>
        <svg viewBox="0 0 16 16"><path d="M8 0a6 6 0 0 0-6 6c0 4.5 6 10 6 10s6-5.5 6-10a6 6 0 0 0-6-6zm0 8.5A2.5 2.5 0 1 1 8 3.5a2.5 2.5 0 0 1 0 5z"/></svg>
        <span>4180 Lindqvist Ave,<br>Tampa, FL 33482</span>
      </li>
      <li>
        <svg viewBox="0 0 16 16"><path d="M4 0h8a1 1 0 0 1 1 1v14a1 1 0 0 1-1 1H4a1 1 0 0 1-1-1V1a1 1 0 0 1 1-1zm1 2v10h6V2zm3 11a1 1 0 1 0 0 2 1 1 0 0 0 0-2z"/></svg>
        <span>604.781.2249</span>
      </li>
      <li>
        <svg viewBox="0 0 16 16"><path d="M0 3h16v10H0zm1.5 1.2v.3L8 9l6.5-4.5v-.3zM1.5 6v5.8h13V6L8 10.5z"/></svg>
        <span>roheshkamdar@veltrane.com</span>
      </li>
      <li>
        <svg viewBox="0 0 16 16"><path d="M8 0a8 8 0 1 0 0 16A8 8 0 0 0 8 0zm0 1.5c.9 0 2 1.9 2.3 5H5.7C6 3.4 7.1 1.5 8 1.5zM1.6 6.5h2.6c.1-1.8.5-3.4 1.1-4.4A6.5 6.5 0 0 0 1.6 6.5zm0 3a6.5 6.5 0 0 0 3.7 4.4c-.6-1-1-2.6-1.1-4.4zm4.1 0c.3 3.1 1.4 5 2.3 5s2-1.9 2.3-5zm6.1 0c-.1 1.8-.5 3.4-1.1 4.4a6.5 6.5 0 0 0 3.7-4.4zm2.6-3a6.5 6.5 0 0 0-3.7-4.4c.6 1 1 2.6 1.1 4.4z"/></svg>
        <span>www.veltrane.com</span>
      </li>
    </ul>
  </section>

  <section class="card card--back" aria-label="Business card back">
    <div class="brand">Veltrane Group</div>
  </section>

</main>
</body>
</html>
```